Business Cards - New Logo Rebranding

Hello We know have a red and blue logo and are looking to create new cards. We are looking for the best creativity of the new logo merged with some of the existing artwork provided.

Target Market(s)

Realtors

Industry/Entity Type

Real Estate

Contact Information for Business Card

New logo with rebranded colors

Requirements
Must have
• Creative use of the new logo

```html
<!DOCTYPE html>
<html lang="en">
<head>
<meta charset="utf-8">
<title>Summit Group Business Cards</title>
<link href="https://fonts.googleapis.com/css2?family=Montserrat:wght@400;500;600;700;800&display=swap" rel="stylesheet">
<style>
  :root {
    --brand-blue: #0e6fb9;
    --brand-navy: #1a4fa0;
    --brand-red: #e0303c;
    --ink: #3a3a3a;
    --paper: #ffffff;
    --stage-top: #d4d4d4;
    --stage-bottom: #9a9a9a;
    --badge-grey: #c9c6bd;
  }
  * { margin: 0; padding: 0; box-sizing: border-box; }
  html, body { width: 1200px; height: 802px; overflow: hidden; }
  body {
    background: linear-gradient(180deg, var(--stage-top), var(--stage-bottom));
    font-family: "Montserrat", sans-serif;
    position: relative;
  }
  .card {
    position: absolute;
    top: 241px;
    width: 560px;
    height: 320px;
    border-radius: 22px;
    overflow: hidden;
    border-bottom: 6px solid var(--brand-red);
    box-shadow: 0 14px 30px rgba(0,0,0,0.25);
  }
  /* Front */
  .card-front { left: 27px; background: var(--paper); }
  .front-diagonal { position: absolute; inset: 0; }
  .portrait {
    position: absolute; right: 40px; top: 0; width: 200px; height: 150px;
    background: linear-gradient(160deg, #6d6a68 0%, #c79a7e 30%, #1f58b6 55%, #1a4fa0 100%);
  }
  .brand {
    position: absolute; left: 34px; top: 46px;
    display: flex; align-items: center; gap: 10px;
  }
  .brand-dot { width: 42px; height: 42px; border-radius: 50%; background: var(--brand-navy); flex: none; }
  .brand-name { font-weight: 800; font-size: 21px; color: var(--brand-navy); letter-spacing: 0.5px; white-space: nowrap; }
  .person { position: absolute; left: 34px; top: 118px; }
  .person-name { font-weight: 800; font-size: 25px; letter-spacing: 0.5px; }
  .person-name .first { color: var(--brand-navy); }
  .person-name .last { color: var(--brand-red); }
  .person-title { font-size: 15px; font-weight: 500; color: var(--ink); margin-top: 2px; }
  .person-rule { width: 250px; height: 1.5px; background: var(--brand-red); margin: 12px 0 10px; }
  .contact-list { list-style: none; }
  .contact-list li {
    display: flex; align-items: center; gap: 10px;
    font-size: 14px; font-weight: 500; color: var(--ink); line-height: 23px;
  }
  .contact-list svg { width: 14px; height: 14px; fill: var(--brand-blue); flex: none; }
  .services {
    position: absolute; right: 26px; top: 254px; text-align: right;
    font-size: 14px; font-weight: 500; color: var(--ink); line-height: 22px;
  }
  .services .dot { color: var(--brand-red); margin: 0 4px; }
  /* Back */
  .card-back { left: 613px; background: var(--brand-blue); color: #fff; }
  .headline {
    position: absolute; top: 30px; left: 0; right: 0; text-align: center;
    font-weight: 800; font-size: 24px; letter-spacing: 0.5px;
  }
  .headline-rule { position: absolute; top: 82px; left: 0; right: 0; height: 2px; background: var(--brand-red); }
  .why-pill {
    position: absolute; top: 67px; left: 50%; transform: translateX(-50%);
    background: var(--brand-red); border-radius: 16px; padding: 5px 22px;
    font-weight: 700; font-size: 16px; white-space: nowrap;
  }
  .reasons {
    position: absolute; top: 118px; left: 26px; right: 20px;
    display: grid; grid-template-columns: 1fr 1fr; column-gap: 18px;
  }
  .reasons ul { list-style: none; }
  .reasons li {
    position: relative; padding-left: 12px;
    font-size: 13px; font-weight: 600; line-height: 17px; margin-bottom: 9px;
  }
  .reasons li::before {
    content: ""; position: absolute; left: 0; top: 7px;
    width: 4px; height: 4px; border-radius: 50%; background: var(--brand-red);
  }
  .badges {
    position: absolute; right: 22px; bottom: 20px;
    display: flex; align-items: center; gap: 10px;
  }
  .badge-seal { width: 30px; height: 30px; border-radius: 50%; background: var(--badge-grey); border: 2px solid #fff; }
  .badge-seal.gold { background: #d7b23a; }
  .badge-divider { width: 2px; height: 34px; background: var(--brand-red); margin: 0 6px; }
  .badge-tag { width: 54px; height: 20px; background: #2b3f8c; border: 1px solid #d7b23a; }
  .badge-square { width: 22px; height: 22px; background: #fff; }
</style>
</head>
<body>

<section class="card card-front" aria-label="Business card front">
  <svg class="front-diagonal" viewBox="0 0 560 320" preserveAspectRatio="none" aria-hidden="true">
    <line x1="560" y1="118" x2="200" y2="320" stroke="#e0303c" stroke-width="1.5"/>
  </svg>
  <div class="portrait" role="img" aria-label="Portrait photo of the inspector in a blue polo shirt"></div>

  <div class="brand">
    <span class="brand-dot" aria-hidden="true"></span>
    <span class="brand-name">SUMMIT GROUP</span>
  </div>

  <div class="person">
    <h1 class="person-name"><span class="first">MARCO</span> <span class="last">DELGADO</span></h1>
    <p class="person-title">Certified Mold Inspector</p>
    <div class="person-rule"></div>
    <ul class="contact-list">
      <li><svg viewBox="0 0 24 24" aria-hidden="true"><path d="M6.6 10.8a15 15 0 0 0 6.6 6.6l2.2-2.2a1 1 0 0 1 1-.25 11.4 11.4 0 0 0 3.6.57 1 1 0 0 1 1 1V20a1 1 0 0 1-1 1A17 17 0 0 1 3 4a1 1 0 0 1 1-1h3.5a1 1 0 0 1 1 1c0 1.25.2 2.45.57 3.57a1 1 0 0 1-.25 1z"/></svg>800.555.0142</li>
      <li><svg viewBox="0 0 24 24" aria-hidden="true"><path d="M7 1h10a2 2 0 0 1 2 2v18a2 2 0 0 1-2 2H7a2 2 0 0 1-2-2V3a2 2 0 0 1 2-2zm0 3v15h10V4z"/></svg>555.201.7390</li>
      <li><svg viewBox="0 0 24 24" aria-hidden="true"><path d="M2 5h20v14H2zm2 2v.5l8 5 8-5V7l-8 5z"/></svg>marco@summitinspect.com</li>
      <li><svg viewBox="0 0 24 24" aria-hidden="true"><path d="M12 2a10 10 0 1 0 0 20 10 10 0 0 0 0-20zm-1 2.1V8H7.4A8 8 0 0 1 11 4.1zm2 0A8 8 0 0 1 16.6 8H13zM4.3 10H11v4H4.3a8 8 0 0 1 0-4zm8.7 0h6.7a8 8 0 0 1 0 4H13zm-5.6 6H11v3.9A8 8 0 0 1 7.4 16zm5.6 0h3.6a8 8 0 0 1-3.6 3.9z"/></svg>www.SummitInspect.com</li>
    </ul>
  </div>

  <p class="services">
    <span class="dot">•</span>Home<span class="dot">•</span>Sewer<span class="dot">•</span>Mold<span class="dot">•</span>Roof<br>
    <span class="dot">•</span>Commercial<span class="dot">•</span>Termite
  </p>
</section>

<section class="card card-back" aria-label="Business card back">
  <h2 class="headline">THE WEST'S #1 INSPECTION COMPANY!</h2>
  <div class="headline-rule"></div>
  <p class="why-pill">Why Choose the Summit Group</p>

  <div class="reasons">
    <ul>
      <li>Performing Inspections Since 1984</li>
      <li>HomeCert Certified Master / Professional Inspectors®</li>
      <li>500,000+ Inspections Completed Statewide</li>
      <li>90-Day Inspection Guarantees</li>
    </ul>
    <ul>
      <li>Request of Repairs Pricer Report</li>
      <li>AeroCert Drone Licensed Roof Inspectors upon request</li>
      <li>5,000+ 5-Star Reviews on Searchly &amp; Reviewly</li>
    </ul>
  </div>

  <div class="badges" aria-label="Certifications and review listings">
    <span class="badge-seal"></span>
    <span class="badge-seal gold"></span>
    <span class="badge-seal"></span>
    <span class="badge-divider"></span>
    <span class="badge-tag"></span>
    <span class="badge-square"></span>
    <span class="badge-square"></span>
  </div>
</section>

</body>
</html>
```